Catalogue Design Project

We need a catalog design for a new private university called Redwell Institute Bayshore (see website www.rwi-bs.org). The catalog should be about 30 pages maximum and will include items such as General Information, Academic schedule, department descriptions, program descriptions, course descriptions, school policies, student services, admissions, San diego Lifestyle, etc.
I will provide the text but I need a professional design with regard to page layouts. I have provided some examples.
Ok, i posted the catalog content, just missing course descriptions.
Target Market(s)
Young Professionals, Foreign Students
Industry/Entity Type
University
Look and feel
Each slider illustrates characteristics of the customer's brand and the style your logo design should communicate.

```html
<!DOCTYPE html>
<html lang="en">
<head>
<meta charset="utf-8">
<title>E-Commerce/Online Marketing Certificate – Redwell Institute</title>
<link href="https://fonts.googleapis.com/css2?family=Carlito:wght@400;700&display=swap" rel="stylesheet">
<style>
  :root {
    --brand-blue: #2f6aa1;
    --brand-blue-dark: #2a5f95;
    --ink: #1a1a1a;
    --rule: #6f95bd;
    --footer-grey: #8a8a8a;
    --paper: #ffffff;
    --photo-warm: #e9dcc0;
    --photo-light: #f6efe0;
  }
  * { margin: 0; padding: 0; box-sizing: border-box; }
  html, body { width: 927px; height: 1200px; overflow: hidden; background: var(--paper); }
  body { font-family: "Carlito", "Calibri", sans-serif; color: var(--ink); }
  .page { position: relative; width: 927px; height: 1200px; overflow: hidden; }

  .brand-mark {
    position: absolute; left: 60px; top: 38px;
    display: flex; align-items: center; gap: 10px;
    font-size: 19px; font-weight: 700; color: var(--brand-blue);
  }
  .brand-mark .dot { width: 18px; height: 18px; border-radius: 50%; background: var(--brand-blue); }

  .header-photo {
    position: absolute; left: 560px; top: 0; width: 367px; height: 96px;
    background: linear-gradient(90deg, rgba(255,255,255,1) 0%, var(--photo-light) 30%, var(--photo-warm) 70%, #d9c7a2 100%);
  }
  .header-rule { position: absolute; left: 0; top: 100px; width: 927px; height: 2px; background: var(--rule); }
  .section-banner { position: absolute; left: 528px; top: 102px; }
  .section-banner span {
    position: absolute; left: 40px; top: 0; height: 38px; line-height: 40px;
    color: #fff; font-size: 30px; letter-spacing: 0.5px; white-space: nowrap;
  }

  .program-title {
    position: absolute; left: 0; width: 927px; top: 196px;
    text-align: center; font-size: 26px; font-weight: 700;
  }
  .program-intro {
    position: absolute; left: 80px; width: 803px; top: 230px;
    font-size: 20px; line-height: 37px; text-align: justify;
  }
  .meta { position: absolute; left: 80px; font-size: 20px; line-height: 24px; }
  .meta b { font-weight: 700; }
  .course-block { position: absolute; left: 80px; font-size: 20px; line-height: 27px; }
  .course-block h2, .outcome h2 { font-size: 20px; font-weight: 400; text-decoration: underline; }
  .course-block ul { list-style: none; }
  .outcome {
    position: absolute; left: 80px; width: 803px; top: 918px;
    font-size: 20px; line-height: 28px;
  }
  .outcome p { text-align: justify; }

  .footer-rule { position: absolute; left: 0; top: 1156px; width: 927px; height: 1px; background: var(--rule); }
  .footer-folio {
    position: absolute; right: 36px; top: 1170px;
    font-size: 14px; color: var(--footer-grey); letter-spacing: 0.3px;
  }
</style>
</head>
<body>
<div class="page">
  <div class="brand-mark"><span class="dot"></span><span>Redwell Institute</span></div>

  <div class="header-photo" role="img" aria-label="Photograph of an open book on a desk, fading into the page"></div>
  <div class="header-rule"></div>
  <div class="section-banner">
    <svg width="399" height="38" viewBox="0 0 399 38" aria-hidden="true">
      <polygon points="0,0 399,0 399,38 28,38" fill="var(--brand-blue-dark)"/>
    </svg>
    <span>CERTIFICATE PROGRAMS</span>
  </div>

  <h1 class="program-title">E-Commerce/Online Marketing Certificate</h1>
  <p class="program-intro">The E-Commerce Certificate program is created for students wanting to develop the skills necessary to produce successful commerce sites for business. Students will have the opportunity to design actual e-commerce sites, implement them, and after examination evaluate their strengths and weaknesses. Coursework will involve an overview of marketing, legal ramifications of online processing, and the trained use of the latest technologies in both hardware and software.</p>

  <p class="meta" style="top:456px;"><b>Hours:</b> 6 hours per week</p>
  <p class="meta" style="top:493px;"><b>Length:</b> 8 weeks per course</p>

  <section class="course-block" style="top:553px;">
    <h2>Required Courses:</h2>
    <ul>
      <li>MKT 603 Internet Advertising Solutions</li>
      <li>MKT 606 E-Commerce</li>
      <li>COMP 600 Website Creation</li>
      <li>BUS 610 Business Legalities</li>
    </ul>
  </section>

  <section class="course-block" style="top:727px;">
    <h2>Elective Courses: (Choose 1)</h2>
    <ul>
      <li>MKT 602 Marketing Research</li>
      <li>MKT 607 Marketing Internship</li>
      <li>BUS 600 Starting Your Own Business</li>
      <li>COMP 601 Internet Technology</li>
      <li>COMP 602 Introduction to Java Script</li>
    </ul>
  </section>

  <section class="outcome">
    <h2>Learning Outcome:</h2>
    <p>Graduates will be able to create a professional website, use search engine optimization, and make their products as visible as possible to the target market and therefore produce a successful business online.</p>
  </section>

  <div class="footer-rule"></div>
  <p class="footer-folio">13::: REDWELL INSTITUTE</p>
</div>
</body>
</html>
```